Redesign business cards

We have a new logo and I am not that happy with the layout of our existing card and looking for a change. Font is a bit small and the green can be hard to read. Logo may need a tidy up as the copy I have is not that hi-res too so require you to produce a hi-res version of the logo for us too. There will be three individual business cards to produce with just the names and phone numbers being different. Address will change too, but use what you see on the card for now.

Industry/Entity Type

Business

Requirements
Nice to have
• You could consider a redesign to the new logo, just not too radical. We like the blue and green hexagons as we feel that they are representative of oil industry that we are in.

```html
<!DOCTYPE html>
<html lang="en">
<head>
<meta charset="utf-8">
<title>Ferrolux Oil Services – Business Cards</title>
<link rel="stylesheet" href="https://fonts.googleapis.com/css2?family=Open+Sans:wght@400;600;700;800&display=swap">
<style>
  :root {
    --bg: #ece9e4;
    --card-white: #ffffff;
    --brand-green: #8dc63f;
    --brand-blue: #12a3e0;
    --accent-orange: #f39019;
    --text-grey: #6d6e71;
    --text-white: #ffffff;
  }
  * { box-sizing: border-box; margin: 0; padding: 0; }
  html, body { width: 1200px; height: 829px; overflow: hidden; }
  body {
    background: var(--bg);
    font-family: "Open Sans", Arial, sans-serif;
    position: relative;
  }
  .card {
    position: absolute;
    top: 254px;
    width: 540px;
    height: 320px;
    border-radius: 4px;
    box-shadow: 0 6px 18px rgba(0,0,0,0.18);
    overflow: hidden;
  }
  .card-front { left: 45px; background: var(--card-white); }
  .card-back { left: 615px; background: var(--brand-green); }

  .front-waves { position: absolute; inset: 0; }

  .brand-name {
    position: absolute;
    left: 30px;
    top: 96px;
    color: var(--brand-green);
    font-weight: 800;
    line-height: 1;
  }
  .brand-name .brand-main {
    display: flex;
    align-items: center;
    gap: 8px;
    font-size: 40px;
    letter-spacing: -1px;
  }
  .brand-mark {
    width: 12px;
    height: 12px;
    border-radius: 50%;
    background: var(--brand-blue);
  }
  .brand-name .brand-sub { display: block; font-size: 20px; margin-top: 2px; }

  .person {
    position: absolute;
    left: 30px;
    top: 176px;
  }
  .person-name, .person-credentials {
    color: var(--accent-orange);
    font-weight: 700;
    font-size: 16px;
    line-height: 1.2;
  }
  .person-role {
    color: var(--text-grey);
    font-weight: 600;
    font-size: 12.5px;
    margin-top: 3px;
  }

  .contact-list {
    position: absolute;
    right: 22px;
    top: 26px;
    list-style: none;
    color: var(--text-white);
    font-size: 11.5px;
    text-align: right;
    line-height: 1.75;
  }
  .contact-list li { display: flex; justify-content: flex-end; align-items: center; gap: 6px; }
  .contact-list svg { width: 11px; height: 11px; fill: var(--text-white); }

  .address {
    position: absolute;
    right: 22px;
    top: 158px;
    color: var(--text-white);
    font-size: 11.5px;
    text-align: right;
    line-height: 1.5;
  }

  .back-brand {
    position: absolute;
    left: 0; right: 0;
    top: 112px;
    text-align: center;
    color: var(--text-white);
    font-weight: 800;
    font-size: 44px;
    letter-spacing: -1px;
  }
  .back-web {
    position: absolute;
    right: 40px;
    bottom: 40px;
    color: var(--text-white);
    font-size: 15px;
    letter-spacing: 4px;
  }
</style>
</head>
<body>

  <section class="card card-front">
    <svg class="front-waves" viewBox="0 0 540 320" width="540" height="320" aria-hidden="true">
      <path d="M540 0 L327 0 C297 60 257 150 197 214 C147 266 77 290 0 296 L0 320 L540 320 Z" fill="var(--brand-green)"/>
      <path d="M540 0 L339 0 C309 60 269 150 209 218 C159 272 89 298 0 306 L0 320 L540 320 Z" fill="var(--card-white)"/>
      <path d="M540 0 L345 0 C315 60 275 150 215 220 C165 275 95 302 0 312 L0 320 L540 320 Z" fill="var(--brand-blue)"/>
    </svg>

    <div class="brand-name">
      <span class="brand-main">Ferrolux <span class="brand-mark"></span></span>
      <span class="brand-sub">Oil Services</span>
    </div>

    <div class="person">
      <p class="person-name">Daniel Whitford</p>
      <p class="person-credentials">NZCE (Mech) P&amp;P</p>
      <p class="person-role">Director</p>
    </div>

    <ul class="contact-list">
      <li>
        <svg viewBox="0 0 24 24"><path d="M6.6 10.8a15 15 0 0 0 6.6 6.6l2.2-2.2c.3-.3.7-.4 1-.2 1.1.4 2.3.6 3.6.6.6 0 1 .4 1 1V20c0 .6-.4 1-1 1A17 17 0 0 1 3 4c0-.6.4-1 1-1h3.5c.6 0 1 .4 1 1 0 1.3.2 2.5.6 3.6.1.3 0 .7-.2 1z"/></svg>
        +61 400 555 018
      </li>
      <li>
        <svg viewBox="0 0 24 24"><path d="M2 5h20v14H2z"/></svg>
        daniel@ferrolux.co.nz
      </li>
      <li>
        <svg viewBox="0 0 24 24"><circle cx="12" cy="12" r="10"/></svg>
        www.ferrolux.com.au
      </li>
    </ul>

    <div class="address">
      <p>Ferrolux Oil Services 412 Harbour Road</p>
      <p>PO Box 5170 | Kelvin Grove Queensland 4059</p>
    </div>
  </section>

  <section class="card card-back">
    <p class="back-brand">Ferrolux</p>
    <p class="back-web">www.ferrolux.com.au</p>
  </section>

</body>
</html>
```